Business cards to launch an education platform

Hi,
I am looking at having new business cards designed.
I am a startup, developing a web platform for schools and university, the education world. It's an online assessment system.
I would like a card that looks classy, and that is using the colors and the font of my logo.

I have attached:
1) my logo
2) A business card that I have designed quickly so you can have all the information required in the card, but I really don't like it.
3) The font that I am using (Lato Regular) to design my web platform
4) Some screenshots of my web platform so you can have a look at the style that I have.

Target Market(s)

Major market: Education system: Schools and university
Minor markets: Business in general

Industry/Entity Type

Business

Contact Information for Business Card

Clara Fenwick
Director

M: 0437 518 902
E: clara.fenwick@amberLoomSystems.com.au

Requirements
Must have
• The colors of my logo

```html
<!DOCTYPE html>
<html lang="en">
<head>
<meta charset="utf-8">
<title>Amber Loom Systems – Business Cards</title>
<link rel="stylesheet" href="https://fonts.googleapis.com/css2?family=Lato:wght@400;700&display=swap">
<style>
  :root {
    --backdrop: #ecebe8;
    --sky: #2bb2e6;
    --navy: #1b4f8e;
    --accent: #35a9e0;
    --ink: #4a4f57;
    --paper: #ffffff;
  }
  * { box-sizing: border-box; margin: 0; padding: 0; }
  html, body {
    width: 1200px; height: 950px; overflow: hidden;
    background: var(--backdrop);
    font-family: "Lato", Arial, sans-serif;
  }
  .stage { position: relative; width: 1200px; height: 950px; }
  .card {
    position: absolute; width: 580px; height: 350px;
    box-shadow: 0 6px 18px rgba(0,0,0,0.18);
  }
  /* Front: brand side */
  .card--front {
    left: 70px; top: 80px; background: var(--sky); color: var(--paper);
    display: flex; flex-direction: column; align-items: center; justify-content: center;
  }
  .brand { display: flex; align-items: center; gap: 16px; }
  .brand__square { width: 46px; height: 46px; background: var(--paper); }
  .brand__name { font-size: 34px; font-weight: 400; letter-spacing: 2px; color: var(--paper); }
  .card--front .website {
    margin-top: 70px; font-size: 15px; letter-spacing: 3px;
  }
  /* Back: contact side */
  .card--back { left: 550px; top: 520px; background: var(--paper); }
  .card--back .brand { position: absolute; left: 44px; top: 54px; }
  .card--back .brand__square { width: 70px; height: 70px; background: var(--navy); }
  .card--back .brand__name { color: var(--navy); font-size: 32px; letter-spacing: 1.5px; }
  .person { position: absolute; left: 250px; top: 160px; text-align: center; }
  .person__name { font-size: 20px; font-weight: 700; color: var(--navy); letter-spacing: 0.5px; }
  .person__role { margin-top: 6px; font-size: 13px; color: var(--accent); letter-spacing: 1px; }
  .contact { position: absolute; left: 170px; top: 250px; list-style: none; }
  .contact__item {
    display: flex; align-items: center; gap: 10px;
    font-size: 15px; color: var(--ink); margin-bottom: 20px;
  }
  .contact__item:first-child { margin-left: 70px; }
  .contact__icon { width: 16px; height: 16px; flex: none; }
</style>
</head>
<body>
<main class="stage">
  <section class="card card--front">
    <div class="brand">
      <span class="brand__square"></span>
      <span class="brand__name">AMBER LOOM SYSTEMS</span>
    </div>
    <p class="website">www.amberLoomSystems.com.au</p>
  </section>

  <section class="card card--back">
    <div class="brand">
      <span class="brand__square"></span>
      <span class="brand__name">AMBER LOOM SYSTEMS</span>
    </div>
    <div class="person">
      <p class="person__name">CLARA FENWICK</p>
      <p class="person__role">DIRECTOR</p>
    </div>
    <ul class="contact">
      <li class="contact__item">
        <svg class="contact__icon" viewBox="0 0 16 16" aria-hidden="true">
          <rect x="3.5" y="1" width="9" height="14" rx="1.5" fill="none" stroke="#1b4f8e" stroke-width="1.8"/>
          <rect x="6.5" y="12" width="3" height="1.2" fill="#1b4f8e"/>
        </svg>
        <span>0437 518 902</span>
      </li>
      <li class="contact__item">
        <svg class="contact__icon" viewBox="0 0 16 16" aria-hidden="true">
          <rect x="1" y="3" width="14" height="10" fill="#1b4f8e"/>
          <path d="M1 3 L8 9 L15 3" fill="none" stroke="#ffffff" stroke-width="1.2"/>
        </svg>
        <span>clara.fenwick@amberLoomSystems.com.au</span>
      </li>
    </ul>
  </section>
</main>
</body>
</html>
```